holloway paving service

Needs to have phone number 0418259730 and email markholloway@brightmail.com.au.
ABN 62318470915
name mark holloway

For all your concreting solutions
Excavation
Exposed & colour concrete
House & shed slabs
Driveways
Landing & steps

Contact Information for Business Card

ph 0418259730
email markholloway@brightmail.com.au.
ABN 62318470915
name mark holloway

```html
<!DOCTYPE html>
<html lang="en">
<head>
<meta charset="utf-8">
<title>Holloway Paving Service – Business Card</title>
<link rel="stylesheet" href="https://fonts.googleapis.com/css2?family=Roboto+Condensed:wght@400;700&display=swap">
<style>
  :root {
    --page: #e9e7e3;
    --paper: #f7f7f5;
    --slate: #616264;
    --orange: #ec6b1e;
    --ink: #5a5b5d;
    --white: #ffffff;
  }
  * { box-sizing: border-box; margin: 0; padding: 0; }
  html, body { width: 1200px; height: 886px; overflow: hidden; }
  body {
    background: var(--page);
    font-family: "Roboto Condensed", "Arial Narrow", sans-serif;
    position: relative;
  }
  .card {
    position: absolute;
    top: 289px;
    width: 540px;
    height: 308px;
    overflow: hidden;
    box-shadow: 0 6px 18px rgba(0,0,0,.18);
  }
  /* Front */
  .card--front { left: 40px; background: var(--paper); }
  .card--front .edge-bands { position: absolute; inset: 0; }
  .brand {
    position: absolute;
    left: 62px; top: 112px;
    display: flex; align-items: center; gap: 12px;
  }
  .brand__square { width: 38px; height: 38px; background: var(--orange); }
  .brand__divider { width: 1.5px; height: 78px; background: var(--orange); }
  .brand__text { display: flex; flex-direction: column; gap: 4px; }
  .brand__name {
    color: var(--orange); font-weight: 700; font-size: 15px;
    letter-spacing: .3px; line-height: 1.15; text-transform: uppercase;
  }
  .brand__phone { color: var(--orange); font-size: 13px; letter-spacing: 1px; }
  .person { position: absolute; left: 272px; top: 70px; }
  .person__name {
    color: var(--orange); font-weight: 700; font-size: 22px;
    text-transform: uppercase; letter-spacing: .3px; margin-bottom: 14px;
  }
  .contact { list-style: none; }
  .contact li {
    display: flex; align-items: center; gap: 8px;
    color: var(--ink); font-size: 13px; line-height: 22px;
    white-space: nowrap;
  }
  .contact svg { width: 12px; height: 12px; flex: none; }
  .contact .abn { padding-left: 20px; margin-top: 6px; }

  /* Back */
  .card--back { left: 620px; background: var(--slate); }
  .back-brand {
    position: absolute; left: 0; right: 0; top: 70px;
    display: flex; align-items: center; justify-content: center; gap: 14px;
  }
  .back-brand__square { width: 54px; height: 54px; background: var(--orange); }
  .back-brand__name {
    color: var(--white); font-weight: 700; font-size: 24px;
    text-transform: uppercase; letter-spacing: .5px; line-height: 1.1;
  }
  .services { position: absolute; left: 180px; top: 160px; list-style: none; }
  .services li {
    color: var(--white); font-size: 14px; line-height: 21px;
    display: flex; align-items: center; gap: 10px;
  }
  .services li::before {
    content: ""; width: 5px; height: 5px; border-radius: 50%;
    background: var(--orange); flex: none;
  }
</style>
</head>
<body>

<section class="card card--front" aria-label="Business card front">
  <svg class="edge-bands" viewBox="0 0 540 308" preserveAspectRatio="none" aria-hidden="true">
    <rect x="0" y="0" width="46" height="308" fill="var(--slate)"/>
    <polygon points="518,0 540,0 540,308 468,308" fill="var(--orange)"/>
  </svg>

  <div class="brand">
    <span class="brand__square" aria-hidden="true"></span>
    <span class="brand__divider" aria-hidden="true"></span>
    <div class="brand__text">
      <span class="brand__name">Holloway Paving<br>Service</span>
      <span class="brand__phone">0418259730</span>
    </div>
  </div>

  <div class="person">
    <h1 class="person__name">Mark Holloway</h1>
    <ul class="contact">
      <li>
        <svg viewBox="0 0 12 12" aria-hidden="true"><path d="M3 1 L5 3.5 L4 5 Q5 7 7 8 L8.5 7 L11 9 L9.5 11 Q5 11 2.5 8 Q1 5.5 1 2.5 Z" fill="var(--orange)"/></svg>
        0418259730
      </li>
      <li>
        <svg viewBox="0 0 12 12" aria-hidden="true"><rect x="0.5" y="2" width="11" height="8" fill="var(--orange)"/><path d="M1 2.5 L6 6.5 L11 2.5" stroke="#fff" stroke-width="1" fill="none"/></svg>
        markholloway@brightmail.com.au
      </li>
      <li>
        <svg viewBox="0 0 12 12" aria-hidden="true"><circle cx="6" cy="6" r="5.5" fill="var(--orange)"/><path d="M0.5 6 H11.5 M6 0.5 Q3 6 6 11.5 M6 0.5 Q9 6 6 11.5" stroke="#fff" stroke-width=".8" fill="none"/></svg>
        www.hollowaypaving.com.au
      </li>
      <li class="abn">ABN 62318470915</li>
    </ul>
  </div>
</section>

<section class="card card--back" aria-label="Business card back">
  <div class="back-brand">
    <span class="back-brand__square" aria-hidden="true"></span>
    <span class="back-brand__name">Holloway Paving<br>Service</span>
  </div>
  <ul class="services">
    <li>Excavation</li>
    <li>Exposed &amp; colour concrete</li>
    <li>House &amp; shed slabs</li>
    <li>Driveways</li>
    <li>Landing &amp; steps</li>
  </ul>
</section>

</body>
</html>
```